Laser Tattoo Removal Business Cards

We are looking for a professional business card design for a laser tattoo removal business. Ideally looking for a black business card design. The name of the business is Brightline Tattoo Removal. We place our cards at local tattoo shops so we ideally are looking for something trendy/edgy to draw both male and female clientele in.

Target Market(s)

Male/Female ages 18-60

Contact Information for Business Card

black background ideally.. hoping to stay within greys, whites and black

Font styles to use
Serif
Sans Serif

Colors
121212
a9a9a9
5c5c5c
f5f5f5
ffffff
7f7f7f
606060
848484
9d9d9d

Requirements
Must have
• Employee Info:
• Melissa Thornbury
• Chief Executive Offer
• m: 919.537.2846
• w: 919.362.4178
• f: 919.685.3907
• mthornbury@brightlinetattooremoval.example
• Address:
• 4615 Oakmere Pkwy, Suite 210
• Raleigh, NC 27654
• Website:
• www.brightlinetattooremoval.example
Nice to have
• Myabe business name on back or logo on back and employee info on the front

```html
<!DOCTYPE html>
<html lang="en">
<head>
<meta charset="utf-8">
<title>Brightline Tattoo Removal – Business Cards</title>
<link rel="stylesheet" href="https://fonts.googleapis.com/css2?family=Roboto:wght@400;500&family=Roboto+Condensed:wght@400;500&display=swap">
<style>
  :root {
    --stage: #d9d9d9;
    --card: #000000;
    --ink: #ffffff;
    --ink-soft: #f5f5f5;
    --rule: #f5f5f5;
    --tab: #ffffff;
  }
  * { margin: 0; padding: 0; box-sizing: border-box; }
  html, body {
    width: 1200px; height: 960px; overflow: hidden;
    background: var(--stage);
  }
  .canvas { position: relative; width: 1200px; height: 960px; }

  .card {
    position: absolute; left: 313px; width: 600px; height: 342px;
    background: var(--card); color: var(--ink);
    font-family: "Roboto", Arial, sans-serif;
    text-align: center;
  }
  .card--front { top: 113px; }
  .card--back { top: 472px; }

  .tab {
    position: absolute; background: var(--tab);
  }
  .tab--top {
    top: 0; left: 204px; width: 206px; height: 6px;
    border-radius: 0 0 12px 12px;
  }
  .tab--bottom {
    bottom: 0; left: 134px; width: 324px; height: 6px;
    border-radius: 12px 12px 0 0;
  }

  .employee { position: absolute; top: 38px; left: 0; right: 0; }
  .employee__name {
    font-family: "Roboto Condensed", "Arial Narrow", sans-serif;
    font-weight: 500; font-size: 21px; letter-spacing: 0.3px; line-height: 24px;
  }
  .employee__title { font-size: 14.5px; line-height: 18px; color: var(--ink-soft); }

  .contact {
    position: absolute; top: 212px; left: 150px; width: 300px;
    font-size: 14px; color: var(--ink-soft);
  }
  .contact__address { line-height: 20px; white-space: nowrap; margin-left: -12px; margin-right: -12px; }
  .contact__phones {
    margin-top: 7px; padding: 4px 0 3px;
    border-top: 1px solid var(--rule); border-bottom: 1px solid var(--rule);
    line-height: 18px; white-space: nowrap;
  }
  .contact__email { margin-top: 8px; line-height: 18px; font-size: 13.5px; white-space: nowrap; margin-left: -20px; margin-right: -20px; }
  .website {
    font-size: 13.5px; letter-spacing: 2.6px; line-height: 20px; white-space: nowrap;
    color: var(--ink-soft);
  }
  .contact .website { margin-left: -30px; margin-right: -30px; }

  .brand {
    position: absolute; top: 104px; left: 0; right: 0;
    font-family: "Roboto Condensed", "Arial Narrow", sans-serif;
    font-weight: 500; color: var(--ink);
  }
  .brand__name { font-size: 44px; letter-spacing: 4px; line-height: 52px; }
  .brand__mark {
    display: block; margin: 12px auto 14px; width: 10px; height: 10px;
    background: var(--ink);
  }
  .brand__tagline { font-size: 20px; letter-spacing: 4px; line-height: 24px; }
  .card--back .website { position: absolute; top: 290px; left: 0; right: 0; }
</style>
</head>
<body>
<main class="canvas">
  <section class="card card--front" aria-label="Card front">
    <span class="tab tab--top"></span>
    <div class="employee">
      <h1 class="employee__name">MELISSA THORNBURY</h1>
      <p class="employee__title">Chief Executive Offer</p>
    </div>
    <div class="contact">
      <p class="contact__address">4615 Oakmere Pkwy, Suite 210, Raleigh, NC 27654</p>
      <p class="contact__phones">919.362.4178 | 919.537.2846| 919.685.3907</p>
      <p class="contact__email">mthornbury@brightlinetattooremoval.example</p>
      <p class="website">www.brightlinetattooremoval.example</p>
    </div>
    <span class="tab tab--bottom"></span>
  </section>

  <section class="card card--back" aria-label="Card back">
    <div class="brand">
      <p class="brand__name">BRIGHTLINE</p>
      <span class="brand__mark"></span>
      <p class="brand__tagline">TATTOO REMOVAL</p>
    </div>
    <p class="website">www.brightlinetattooremoval.example</p>
  </section>
</main>
</body>
</html>
```